Label design - Superfood blend

We are a family owned nutrition company with big ambitions. Our goal is to develop a range of 100% natural supplements for women, inspired by nature & modern technology that helps them meet their nutritional needs while nourishing them from within. All our products are junk free because we believe that that’s how nature intended it. We also produce products through a sustainable process and only use biodegradable packaging for our products (See link - https://www.loamwrap.org.uk/biodegradable-stand-pouch-250g-kraft)

Our brand style is modern and minimalist. This same style will be reflected in our social media, website and we want it to be represented through the label designs for our product packaging.

We want some creative designers to design a label that is true to our style (See attached packaging brief with designs we like) and displays our values of Premium, High Quality, Organic Real Food supplements focused on women. I have provided examples in the attached brief, but please only use as inspiration, I dont want any of them to be copied (sorry have had my fingers burnt already !)
Updates

Hello all, Please note this design is for a LABEL and not the whole package. We will have a 500gm biodegradable brown package, and we will have a label (which is what this project is about) that will be stuck on the front. The size of the label will be a rectangle (unless you come up with a new shape) in the size 20cm * 15cm. Please do not submit designs for the WHOLE from of the package, as we dont intend to have printed packages. Regards

Hello all, I have added a new logo version to the attachments, could you please also try that version. Could you also please look at the new sliders. We are only looking for a minimlaist theme. If you dont know what that means, please do feel free to ask, I would be happy to supply examples. Minimalist designs, means clean, modern, upmarket, elegant designs. It does not use too many colors and mostly sticks to a combination of black and white with colors used sparingly. See some below for your reference anyway. https://www.pitchloft.co.uk/design/13359317 https://www.pitchloft.co.uk/design/17270649 https://www.pitchloft.co.uk/design/12584145 https://www.pitchloft.co.uk/design/12367479 https://www.snapquilt.com/search/pins/?q=minimalist%20label%20design&rs=rs&eq=&etslf=2809&term_meta[]=minimalist%7Crecentsearch%7Cundefined&term_meta[]=label%7Crecentsearch%7Cundefined&term_meta[]=design%7Crecentsearch%7Cundefined Regards

Target Market(s)

The target market is women between the age 25 to 45, based in UK (mostly based in larger cities in UK). They are typically middle class or higher and would be in demanding jobs and social lives, that requires for them to meet their nutrition needs in convenient, easy to take forms. The women would also be socially conscious and sensitive to issues like women's rights, environmental issues, healthy food, organic food and sustainability etc. I have a much more detailed customer avatar if required

Font styles to use
Serif
Sans Serif
Decorative
Script

Colors
e8e8e8
474747
1b1b1b
add136

Requirements
Must have
• The label, should look minimalist and modern, throw in some out of the box creativity and we have a winner. Creativity will definitely be of importance. Our packaging is a biodegradable brown paper stand up pouch (Example link in product description). So to make it standout from other colorful packaging - being creative would definitely help.
• Please use the color schemes provided in the brief (See attachments). But if you want to experiment I would be open to it, as long as they are still minimalist and does not stray very far from the color given in the brief :)

```html
<!DOCTYPE html>
<html lang="en">
<head>
<meta charset="utf-8">
<title>Inner Bloom – Label</title>
<link rel="stylesheet" href="https://fonts.googleapis.com/css2?family=Didact+Gothic&family=Encode+Sans+Semi+Condensed:wght@600&display=swap">
<style>
  :root {
    --backdrop: #ececec;
    --label-paper: #f8f6f0;
    --sage: #a7b891;
    --sage-line: #6f7f62;
    --title-green: #3f5a1e;
    --accent-lime: #a9c23f;
    --ink: #333333;
    --ink-dark: #1b1b1b;
    --muted-olive: #8a9a4a;
    --badge-green: #4f8a3a;
    --badge-dark: #474747;
  }
  html, body {
    margin: 0;
    padding: 0;
    width: 1185px;
    height: 1200px;
    overflow: hidden;
    background: var(--backdrop);
  }
  .canvas {
    position: relative;
    width: 1185px;
    height: 1200px;
  }
  .label {
    position: absolute;
    left: 182px;
    top: 40px;
    width: 820px;
    height: 1120px;
    background: var(--label-paper);
    overflow: hidden;
    box-shadow: 0 2px 10px rgba(0,0,0,0.06);
  }
  .label-texture {
    position: absolute;
    inset: 0;
    background: linear-gradient(160deg, #faf8f2 0%, #f4f1e8 100%);
  }
  .brand-arch {
    position: absolute;
    left: 252px;
    top: 0;
    width: 306px;
    height: 440px;
    background: var(--sage);
    border-radius: 0 0 153px 153px;
  }
  .brand-ring {
    position: absolute;
    left: 276px;
    top: 120px;
    width: 258px;
    height: 258px;
    border: 2px solid var(--sage-line);
    border-radius: 50%;
    box-sizing: border-box;
  }
  .brand-name {
    position: absolute;
    left: 252px;
    width: 306px;
    top: 255px;
    text-align: center;
    font-family: "Didact Gothic", sans-serif;
    font-size: 25px;
    letter-spacing: 5px;
    color: var(--ink-dark);
  }
  .title-frame {
    position: absolute;
    left: 0;
    top: 0;
  }
  .product-title {
    position: absolute;
    margin: 0;
    left: 98px;
    width: 612px;
    top: 518px;
    text-align: center;
    font-family: "Encode Sans Semi Condensed", sans-serif;
    font-weight: 600;
    font-size: 76px;
    line-height: 1;
    color: var(--title-green);
    letter-spacing: 1px;
  }
  .product-descriptor {
    position: absolute;
    left: 0;
    width: 820px;
    top: 758px;
    text-align: center;
    font-family: "Didact Gothic", sans-serif;
    font-size: 24px;
    line-height: 33px;
    letter-spacing: 3.5px;
    color: var(--ink);
    margin: 0;
  }
  .supplement-tag {
    position: absolute;
    left: 0;
    width: 820px;
    top: 920px;
    text-align: center;
    font-family: "Didact Gothic", sans-serif;
    font-size: 24px;
    letter-spacing: 3.5px;
    color: var(--muted-olive);
    margin: 0;
  }
  .net-weight {
    position: absolute;
    left: 50px;
    top: 1052px;
    font-family: "Didact Gothic", sans-serif;
    font-size: 21px;
    letter-spacing: 1px;
    color: var(--ink-dark);
    margin: 0;
  }
  .badge-vegan {
    position: absolute;
    left: 352px;
    top: 1034px;
  }
  .badge-organic {
    position: absolute;
    left: 694px;
    top: 1006px;
  }
</style>
</head>
<body>
<main class="canvas">
  <section class="label" aria-label="Product label">
    <div class="label-texture" role="img" aria-label="Subtle light geometric line pattern on cream paper"></div>

    <div class="brand-arch"></div>
    <div class="brand-ring"></div>
    <div class="brand-name">VERDALUME</div>

    <svg class="title-frame" width="820" height="1120" aria-hidden="true">
      <line x1="94" y1="490" x2="450" y2="490" stroke="var(--accent-lime)" stroke-width="3"/>
      <line x1="450" y1="490" x2="712" y2="490" stroke="var(--ink-dark)" stroke-width="3"/>
      <line x1="710" y1="490" x2="710" y2="612" stroke="var(--ink-dark)" stroke-width="3"/>
      <line x1="96" y1="540" x2="96" y2="628" stroke="var(--ink-dark)" stroke-width="3"/>
      <line x1="94" y1="626" x2="200" y2="626" stroke="var(--ink-dark)" stroke-width="3"/>
    </svg>
    <h1 class="product-title">INNER BLOOM</h1>

    <p class="product-descriptor">ORGANIC, PLANT-BASED<br>PREBIOTICS AND SUPERFOOD BLEND</p>
    <p class="supplement-tag">FOOD SUPPLEMENT</p>

    <p class="net-weight">500gm</p>

    <svg class="badge-vegan" width="106" height="60" aria-label="Vegan certification badge" role="img">
      <rect x="14" y="8" width="78" height="44" rx="22" fill="var(--badge-green)"/>
    </svg>
    <svg class="badge-organic" width="92" height="92" aria-label="Organic certification badge" role="img">
      <circle cx="46" cy="46" r="40" fill="none" stroke="var(--badge-dark)" stroke-width="3"/>
      <circle cx="46" cy="46" r="22" fill="var(--badge-dark)"/>
    </svg>
  </section>
</main>
</body>
</html>
```